Website redesign for AI startup

Overview
We are looking to have our website https://www.hellomarlo.ai/ redesigned to look much more sophisticated and modern. We would like the brand colors to be different and less or no use of the Marlo bird character. We have included some example sites below for designs that we like. Please do not to use the same purple or purple at all on the site as we would like different brand colors and 'too much purple' has been the main comment.

Example sites that we like:
https://www.quorvant.com/
https://pagemorrow.com/
https://www.steadycloudly.com/

Requirements
Redesign the following pages from our website, modeling an example site that we like:
-Home page: https://hellomarlo.ai
-See an example: https://www.hellomarlo.ai/example-page
-Pricing: https://www.hellomarlo.ai/pricing
-Product: https://www.hellomarlo.ai/how-it-works
-Portal home: https://www.hellomarlo.ai/overview (you will need to create an account to view this; the account is free)
New design should be sleek, professional, and modern
The pages should contain the same content that it currently does.
Images on the pages should change to match the new designs and style.
Use different brand colors, these should look professional
The Marlo bird character can be used, but it’s not required. If the bird is used, it should be rarely used and not front-and-center.
Provide both desktop and mobile designs

Target Market(s)

Small business owners

Industry/Entity Type

SaaS tool

Number of Pages Required

5+ page

Requirements
Must have
• modern and sleek design, different brand colors, mobile and web designs

```html
<!DOCTYPE html>
<html lang="en">
<head>
<meta charset="UTF-8">
<title>Marlo – AI Sales Assistant</title>
<link href="https://fonts.googleapis.com/css2?family=Inter:wght@400;500;600;700;800&display=swap" rel="stylesheet">
<style>
:root{
  --bg-top:#0a1222;
  --bg-mid:#05080f;
  --black:#000;
  --blue:#1f6bff;
  --blue-text:#2a72ff;
  --blue-name:#2f6fe6;
  --white:#fff;
  --muted:#a9adb5;
  --panel:#1b1b1c;
  --panel-inner:#2b2a2c;
  --card:#141415;
  --card-border:#1d3b8f;
}
*{margin:0;padding:0;box-sizing:border-box}
html,body{width:1200px;height:3022px;overflow:hidden}
body{
  position:relative;font-family:'Inter',sans-serif;color:var(--white);
  background:
    radial-gradient(ellipse 700px 500px at 200px 1750px, rgba(20,50,110,.45), transparent 70%),
    radial-gradient(ellipse 900px 420px at 600px 2820px, rgba(20,60,140,.35), transparent 70%),
    linear-gradient(180deg,var(--bg-top) 0,#070c18 900px,var(--bg-mid) 1600px,var(--black) 2000px,#020611 2700px,#061029 2960px);
}
.abs{position:absolute}
/* header */
.site-header{position:absolute;left:0;top:0;width:1200px;height:118px;border-bottom:1px solid #1d2434}
.brand{position:absolute;left:82px;top:40px;display:flex;align-items:center;gap:12px;font-size:34px;font-weight:700;color:var(--white)}
.brand-mark{width:26px;height:26px;background:var(--blue);border-radius:4px}
.nav{position:absolute;top:51px;left:528px}
.nav a{position:absolute;color:var(--white);text-decoration:none;font-size:16px;white-space:nowrap}
/* buttons */
.btn{position:absolute;background:var(--blue);color:var(--white);font-size:13px;font-weight:700;display:flex;align-items:center;justify-content:center;border-radius:2px;text-decoration:none}
/* hero */
.hero-title{left:82px;top:208px;font-size:60px;font-weight:800;letter-spacing:-.5px}
.hero-sub{left:82px;top:298px;font-size:27px;font-weight:500}
.hero-brand{left:82px;top:345px;font-size:43px;font-weight:800;color:var(--blue)}
.hero-tag{left:82px;top:414px;font-size:21px;font-weight:500}
.hero-media{left:661px;top:178px;width:456px;height:369px;border-radius:22px;
  background:radial-gradient(ellipse at 60% 45%,#1f7f9a 0,#0f4a66 40%,#0a2237 80%)}
.play{left:1070px;top:498px;width:74px;height:74px;border-radius:50%;background:var(--blue);display:flex;align-items:center;justify-content:center}
/* about */
.center{left:0;width:1200px;text-align:center}
.section-title{font-size:60px;font-weight:800;letter-spacing:-.5px}
.about-text{font-size:17px;line-height:34px}
/* features */
.feature-panel{left:613px;top:996px;width:587px;height:632px;background:var(--panel);border-radius:8px 0 0 8px}
.chat{left:645px;top:1028px;width:555px;height:570px;background:var(--panel-inner);border-radius:20px 0 0 0;overflow:hidden}
.bubble{position:absolute;left:39px;width:426px;background:var(--white);border-radius:14px;color:#444;font-size:12.5px;line-height:28px;padding:20px 28px}
.reply{position:absolute;left:386px;width:158px;height:58px;background:var(--blue);border-radius:10px;color:var(--white);font-size:14.5px;display:flex;align-items:center;justify-content:center}
.mascot{position:absolute;left:488px;top:502px;width:58px;height:66px;border-radius:50%;background:radial-gradient(circle,#6fd3df,#2b8fa3)}
.feature-card{left:72px;top:1037px;width:474px;height:184px;background:var(--card);border-bottom:2px solid var(--blue);border-radius:4px}
.feature-card h3{position:absolute;left:97px;top:28px;font-size:21px;font-weight:700}
.feature-card p{position:absolute;left:97px;top:67px;width:340px;font-size:14px;line-height:28px}
.feature-list{left:110px;top:1258px;list-style:none}
.feature-list li{display:flex;align-items:center;height:73px;font-size:19px;color:var(--muted);font-weight:500}
.feature-list svg{width:36px;height:36px;margin-right:23px}
/* testimonials */
.testi-title{left:111px;top:1755px;font-size:60px;font-weight:800;line-height:76px;letter-spacing:-.5px}
.arrows{left:1036px;top:1830px}
.review{position:absolute;top:1971px;width:339px;height:457px;border:1px solid var(--card-border);border-radius:6px;background:linear-gradient(180deg,#070a12,#000)}
.review .quote{position:absolute;left:32px;top:50px;font-size:72px;font-weight:800;color:var(--card-border);line-height:1}
.review p{position:absolute;left:32px;top:107px;width:296px;font-size:15px;line-height:33px;letter-spacing:-.1px}
.review .who{position:absolute;left:31px;top:300px;font-size:16px;color:var(--blue-name);font-weight:500}
.review .avatar{position:absolute;left:32px;top:342px;width:64px;height:64px;border-radius:50%;background:linear-gradient(135deg,#c9ccd2,#4c5360)}
/* setup */
.eyebrow{font-size:23px;font-weight:600;color:var(--blue-text)}
.setup-text{font-size:19px;line-height:44px}
/* footer */
.site-footer{left:0;top:2961px;width:1200px;height:61px;background:var(--blue)}
.site-footer small{position:absolute;left:110px;top:23px;font-size:13px}
.social{position:absolute;top:24px;width:14px;height:14px;border:2px solid var(--white);border-radius:3px}
</style>
</head>
<body>

<header class="site-header">
  <div class="brand"><span class="brand-mark"></span>Marlo</div>
  <nav class="nav">
    <a style="left:0">Home</a>
    <a style="left:89px">Product</a>
    <a style="left:191px">Support</a>
    <a style="left:296px">Pricing</a>
    <a style="left:390px">FAQ</a>
    <a style="left:465px">Referral Program</a>
  </nav>
</header>

<section>
  <h1 class="abs hero-title">AI Sales Assistant</h1>
  <p class="abs hero-sub">Save time and get more customers with</p>
  <p class="abs hero-brand">Marlo</p>
  <p class="abs hero-tag">Your 24/7 AI Sales Assistant</p>
  <a class="btn" style="left:82px;top:469px;width:150px;height:37px">Create Your Marlo</a>
  <a class="btn" style="left:255px;top:469px;width:150px;height:37px">See An Example</a>
  <div class="abs hero-media" role="img" aria-label="Open hand holding a small friendly robot assistant in front of a glowing teal tech backdrop"></div>
  <div class="abs play"><svg width="24" height="24" viewBox="0 0 24 24"><path d="M6 3l15 9-15 9z" fill="#fff"/></svg></div>
</section>

<section>
  <h2 class="abs center section-title" style="top:668px">About Marlo</h2>
  <p class="abs center about-text" style="top:762px">When a lead engages you via email, phone, chat, or text, you need to get back to them immediately.<br>But how do you do that when you're busy helping other clients?</p>
  <a class="btn" style="left:540px;top:860px;width:120px;height:37px">Get Started</a>
</section>

<section>
  <div class="abs feature-card">
    <svg class="abs" style="left:38px;top:32px" width="38" height="38" viewBox="0 0 38 38"><circle cx="19" cy="19" r="17" fill="none" stroke="#2a72ff" stroke-width="2" stroke-dasharray="70 8"/><text x="19" y="23" font-family="Inter,sans-serif" font-size="11" font-weight="700" fill="#2a72ff" text-anchor="middle">24/7</text></svg>
    <h3>24/7 Customer Engagement</h3>
    <p>Marlo interacts with your leads across email, chatbot, phone, and text around the clock. See an example here.</p>
  </div>
  <ul class="abs feature-list">
    <li><svg viewBox="0 0 36 36" fill="none" stroke="#8a8f99" stroke-width="1.5"><circle cx="9" cy="8" r="4"/><path d="M4 30V18h10v12"/><path d="M20 8h12M20 14h12M20 20h12M20 26h12"/></svg>Lead Qualification &amp; Prioritization</li>
    <li><svg viewBox="0 0 36 36" fill="none" stroke="#8a8f99" stroke-width="1.5"><rect x="3" y="6" width="24" height="22" rx="2"/><path d="M3 12h24M9 3v6M21 3v6"/><circle cx="26" cy="26" r="7" fill="#0a0e18"/><path d="M26 22v4l3 2"/></svg>Automated Scheduling</li>
    <li><svg viewBox="0 0 36 36" fill="none" stroke="#8a8f99" stroke-width="1.5"><circle cx="18" cy="18" r="13"/><circle cx="18" cy="18" r="6"/><path d="M18 5v7M18 24v7M5 18h7M24 18h7"/></svg>Rapid and Effective AI Training</li>
    <li><svg viewBox="0 0 36 36" fill="none" stroke="#8a8f99" stroke-width="1.5"><rect x="5" y="10" width="26" height="18" rx="4"/><circle cx="13" cy="19" r="2"/><circle cx="23" cy="19" r="2"/><path d="M18 10V5"/></svg>Customize Your Assistant</li>
    <li><svg viewBox="0 0 36 36" fill="none" stroke="#8a8f99" stroke-width="1.5"><circle cx="10" cy="18" r="6"/><rect x="20" y="4" width="12" height="28" rx="2"/><path d="M23 10h6M23 16h6M23 22h6"/></svg>Seamless Tool Integration</li>
  </ul>

  <div class="abs feature-panel"></div>
  <div class="abs chat">
    <div class="bubble" style="top:37px">I must explain to you how all this mistaken idea of deno<br>uncing pleasure and praising pain was born and I</div>
    <div class="reply" style="top:154px">Lorem Lipsum</div>
    <div class="bubble" style="top:239px">I must explain to you how all this mistaken idea of deno<br>uncing pleasure and praising pain was born and I<br>will give you a complete account of the system, and expound<br>the actual teachings of the great ???</div>
    <div class="reply" style="top:419px">Lorem Lipsum</div>
    <div class="bubble" style="top:503px">I must explain to you how all this mistaken idea of deno<br>uncing pleasure and praising pain was born and I</div>
    <div class="mascot" role="img" aria-label="Small teal bird mascot peeking in at the chat corner"></div>
  </div>
</section>

<section>
  <h2 class="abs testi-title">What Our Customers<br>Say about us</h2>
  <svg class="abs arrows" width="54" height="16" viewBox="0 0 54 16"><path d="M2 8h16M2 8l5-4M2 8l5 4" stroke="#777" stroke-width="1.6" fill="none"/><path d="M32 8h18M50 8l-5-4M50 8l-5 4" stroke="#fff" stroke-width="2" fill="none"/></svg>

  <article class="review" style="left:113px">
    <div class="quote">”</div>
    <p>Marlo is an incredible time saver for my business! It qualifies leads and gets them on my calendar and it was super easy to set up!</p>
    <div class="who">Owen Pratt, Real Estate Agent</div>
    <div class="avatar" role="img" aria-label="Portrait photo of the reviewer"></div>
  </article>
  <article class="review" style="left:499px">
    <div class="quote">”</div>
    <p>I love that I can collect information about new potential clients as they interact with my ai assistant. Marlo saves me time and helps me build quality relationships with new clients.</p>
    <div class="who">Luis Varga, Photographer</div>
    <div class="avatar" role="img" aria-label="Portrait photo of the reviewer"></div>
  </article>
  <article class="review" style="left:885px">
    <div class="quote">”</div>
    <p>Marlo is a must have for me! A simple add on to my socials and website to capture new leads!! I love the simplicity!</p>
    <div class="who">Nadia Brooks, Real Estate Agent</div>
    <div class="avatar" role="img" aria-label="Portrait photo of the reviewer"></div>
  </article>
</section>

<section>
  <p class="abs center eyebrow" style="top:2562px">SET UP</p>
  <h2 class="abs center section-title" style="top:2596px">Your own Marlo</h2>
  <p class="abs center setup-text" style="top:2694px">How do you avoid the endless churn of back and forths, including with many<br>people who aren't even right for your business?</p>
  <a class="btn" style="left:526px;top:2808px;width:149px;height:37px">Create Your Marlo</a>
</section>

<footer class="abs site-footer">
  <small>(C) Copyright 2024 | All Rights Reserved</small>
  <span class="social" style="left:965px" aria-label="Social link"></span>
  <span class="social" style="left:1001px" aria-label="Social link"></span>
  <span class="social" style="left:1037px" aria-label="Social link"></span>
  <span class="social" style="left:1073px" aria-label="Social link"></span>
</footer>

</body>
</html>
```